Harborline Renewal Business Card Design

Professional and clean design. The design colors should flow with the logo. Two-sided card with the website on the back which is:

www.HarborlineRenewal.example.

"Specializing in Water Damage Restoration"

On the front I need the name, email, phone, and logo.

Name: Darnell Quisby
Email: Darnell@HarborlineRenewal.example
Phone: 555-318-2046 for now

I only have the Preview and Thumbnail right now but should have the source files uploaded within a day or two.

Target Market(s)

Flood victims, home owners with water damage from busted pipes etc...

Industry/Entity Type

Business

Contact Information for Business Card

Name: Darnell Quisby

Font styles to use
Serif
Sans Serif

Requirements
Must have
• Business Card Details Info

```html
<!DOCTYPE html>
<html lang="en">
<head>
<meta charset="utf-8">
<title>Harborline Renewal Business Card</title>
<link rel="stylesheet" href="https://fonts.googleapis.com/css2?family=Cinzel:wght@400;600&family=Open+Sans:wght@400&display=swap">
<style>
  :root {
    --bg: #e9e6e1;
    --card: #ffffff;
    --card-edge: #3a3a3a;
    --blue: #2e8fd4;
    --blue-light: #5bbfee;
    --ink: #2b2b2b;
    --ink-soft: #3d3d3d;
    --rule: #c9c9c9;
  }
  html, body {
    margin: 0;
    padding: 0;
    width: 1200px;
    height: 1188px;
    overflow: hidden;
    background: var(--bg);
  }
  .canvas {
    position: relative;
    width: 1200px;
    height: 1188px;
  }
  .card {
    position: absolute;
    width: 908px;
    height: 518px;
    background: var(--card);
    border: 1.5px solid var(--card-edge);
    border-radius: 34px;
    overflow: hidden;
    box-sizing: border-box;
  }
  .card--front { left: 238px; top: 57px; }
  .card--back  { left: 50px;  top: 629px; }

  .brand-dot {
    position: absolute;
    border-radius: 50%;
    background: var(--blue);
  }
  .brand-name {
    position: absolute;
    margin: 0;
    font-family: "Cinzel", Georgia, serif;
    font-weight: 600;
    color: var(--blue);
    text-align: center;
    letter-spacing: 0.04em;
    line-height: 1.1;
    white-space: nowrap;
  }

  /* front */
  .card--front .brand-dot { left: 176px; top: 112px; width: 108px; height: 108px; }
  .card--front .brand-name { left: 10px; width: 450px; top: 238px; font-size: 31px; }

  .divider {
    position: absolute;
    left: 432px; top: 120px;
    width: 2px; height: 195px;
    background: var(--rule);
  }
  .person {
    position: absolute;
    left: 463px; top: 116px;
  }
  .person-name {
    margin: 0;
    font-family: "Cinzel", Georgia, serif;
    font-weight: 400;
    font-size: 31px;
    color: var(--blue);
    letter-spacing: 0.03em;
  }
  .person-title {
    margin: 2px 0 0;
    font-family: "Cinzel", Georgia, serif;
    font-size: 26px;
    color: var(--ink-soft);
    letter-spacing: 0.06em;
  }
  .contacts {
    position: absolute;
    left: 463px; top: 216px;
    margin: 0; padding: 0;
    list-style: none;
    font-family: "Open Sans", Arial, sans-serif;
    font-size: 21px;
    color: var(--ink);
  }
  .contacts li {
    display: flex;
    align-items: center;
    height: 35px;
  }
  .contacts svg { width: 18px; height: 18px; margin-right: 12px; flex: none; }

  .water-band {
    position: absolute;
    left: 0; bottom: 0;
    width: 908px; height: 118px;
    background: linear-gradient(180deg, var(--blue) 0%, var(--blue-light) 18%, var(--blue-light) 100%);
  }
  .tagline {
    position: absolute;
    left: 40px; width: 420px;
    top: 437px;
    margin: 0;
    font-family: "Cinzel", Georgia, serif;
    font-size: 20px;
    line-height: 1.3;
    text-align: center;
    color: var(--ink);
    letter-spacing: 0.03em;
  }

  /* back */
  .card--back .brand-dot { left: 379px; top: 62px; width: 150px; height: 150px; }
  .card--back .brand-name { left: 0; width: 908px; top: 250px; font-size: 60px; }
  .website {
    position: absolute;
    left: 0; width: 908px;
    top: 380px;
    margin: 0;
    text-align: center;
    font-family: "Open Sans", Arial, sans-serif;
    font-size: 30px;
    letter-spacing: 0.05em;
    color: var(--ink);
  }
</style>
</head>
<body>
<main class="canvas">

  <section class="card card--front" aria-label="Card front">
    <span class="brand-dot" aria-hidden="true"></span>
    <p class="brand-name">Harborline Renewal</p>

    <span class="divider" aria-hidden="true"></span>

    <div class="person">
      <h1 class="person-name">Darnell Quisby</h1>
      <p class="person-title">Title</p>
    </div>

    <ul class="contacts">
      <li>
        <svg viewBox="0 0 20 20" aria-hidden="true"><path d="M5 2 L8 2 L9 6 L7 8 Q9 12 12 13 L14 11 L18 12 L18 15 Q17 18 14 18 Q3 15 2 5 Q2 2 5 2 Z" fill="none" stroke="#2e8fd4" stroke-width="1.8"/></svg>
        555-318-2046
      </li>
      <li>
        <svg viewBox="0 0 20 20" aria-hidden="true"><rect x="1" y="4" width="18" height="12" rx="1.5" fill="#2e8fd4"/><path d="M1.5 5 L10 11 L18.5 5" fill="none" stroke="#fff" stroke-width="1.6"/></svg>
        Darnell@HarborlineRenewal.example
      </li>
      <li>
        <svg viewBox="0 0 20 20" aria-hidden="true"><g fill="none" stroke="#2e8fd4" stroke-width="1.5"><circle cx="10" cy="10" r="8.5"/><ellipse cx="10" cy="10" rx="3.8" ry="8.5"/><path d="M1.5 10 H18.5 M3 5.5 H17 M3 14.5 H17"/></g></svg>
        www.HarborlineRenewal.example
      </li>
    </ul>

    <div class="water-band" role="img" aria-label="Blue water wave band along the bottom of the card"></div>
    <p class="tagline">Specializing in<br>Water Damage Restoration</p>
  </section>

  <section class="card card--back" aria-label="Card back">
    <span class="brand-dot" aria-hidden="true"></span>
    <p class="brand-name">Harborline Renewal</p>
    <p class="website">www.HarborlineRenewal.example</p>
  </section>

</main>
</body>
</html>
```